I need a business card for my original fine art pieces

I would like a business card design including a logo design for a new business in the art world. I am based in the Hunter Valley NSW Australia. I am a contemporary figurative, encaustic and wildlife artist. I would like to be able to upload my email and mobile number to this as well. This design should be one that I can incorporate into banners and flyers etc. Id like to incorporate one of my own images or partial image into the background or somewhere below. My initials are RJ and I would like these used as a logo type. I would like the use of some colour and it to be bright and catchy. The final design should communicate artwork custom made and commissions available.

Overview: Original Fine Artworks for sale, online, art galleries etc, Custom made to order and by commission.

Target market is world wide audience and corporate world

My figurative work is painted using acrylics in a lot of natural ochre colours that reflect the Australian Outback, on canvas, linen, paper or board: My encaustic work is created in a contemporary abstract style using a blow torch and a made with a medium of 100% pure bees wax, Damar resin, mixed media and coloured pigments, applied to Birch board. My wildlife are created using coloured pencil and mixed media on a variety of paper types or board.

```html
<!DOCTYPE html>
<html lang="en">
<head>
<meta charset="utf-8">
<title>Rhea Jarvis – Business Card</title>
<link href="https://fonts.googleapis.com/css2?family=Cinzel:wght@500&family=Crimson+Text&family=Questrial&family=Cabin&display=swap" rel="stylesheet">
<style>
  :root {
    --orange: #ee4b23;
    --black: #000000;
    --white: #ffffff;
    --backdrop: #e6e7e8;
    --ink: #111111;
  }
  * { margin: 0; padding: 0; box-sizing: border-box; }
  html, body { width: 1200px; height: 927px; overflow: hidden; background: var(--backdrop); }
  .stage { position: relative; width: 1200px; height: 927px; }
  .card {
    position: absolute; top: 73px; width: 446px; height: 781px;
    border-radius: 32px; overflow: hidden;
    box-shadow: 6px 8px 10px rgba(0,0,0,0.35);
  }
  .card--front { left: 134px; }
  .card--back { left: 619px; }
  .card__bg { position: absolute; inset: 0; }
  .centered { position: absolute; left: 0; width: 100%; text-align: center; white-space: nowrap; }
  .brand-name { top: 252px; font-family: "Cinzel", serif; font-weight: 500; font-size: 39px; color: var(--orange); line-height: 1; }
  .brand-tag { top: 297px; font-family: "Questrial", sans-serif; font-size: 17px; letter-spacing: 3.6px; color: var(--ink); }
  .back-name { top: 416px; font-family: "Cinzel", serif; font-weight: 500; font-size: 44px; color: var(--orange); line-height: 1; }
  .person { top: 404px; font-family: "Crimson Text", serif; font-size: 37px; color: var(--orange); line-height: 1; }
  .detail { font-family: "Questrial", sans-serif; font-size: 19px; color: var(--ink); line-height: 1; }
  .detail--role { top: 446px; }
  .detail--city { top: 478px; }
  .detail--abn { top: 502px; }
  .detail--phone { top: 565px; }
  .detail--mail { top: 590px; }
  .detail--web { top: 614px; }
  .accent { color: var(--orange); }
  .contact-icons { top: 532px; display: flex; justify-content: center; gap: 6px; }
  .offer { top: 644px; font-family: "Cabin", sans-serif; font-size: 18.5px; line-height: 27px; color: var(--orange); }
  .back-web { top: 706px; font-family: "Questrial", sans-serif; font-size: 23px; letter-spacing: 1px; color: var(--white); }
</style>
</head>
<body>
<main class="stage">

  <section class="card card--front">
    <svg class="card__bg" viewBox="0 0 446 781" width="446" height="781">
      <rect width="446" height="781" fill="var(--black)"/>
      <path d="M0 192 A278 278 0 0 1 446 192 L446 746 L0 746 Z" fill="var(--white)"/>
      <path d="M0 192 A278 278 0 0 1 446 192" fill="none" stroke="var(--orange)" stroke-width="6"/>
      <rect x="0" y="746" width="446" height="35" fill="var(--white)"/>
      <rect x="0" y="746" width="80" height="35" fill="var(--black)"/>
      <rect x="86" y="746" width="274" height="35" fill="var(--orange)"/>
      <rect x="366" y="746" width="80" height="35" fill="var(--black)"/>
    </svg>
    <div class="centered brand-name">Rhea Jarvis</div>
    <div class="centered brand-tag">ORIGINAL FINE ARTWORKS</div>

    <div class="centered person">Rhea Jarvis</div>
    <div class="centered detail detail--role">Director</div>
    <div class="centered detail detail--city">Hunter Valley NSW</div>
    <div class="centered detail detail--abn">ABN 42 118 503 276</div>

    <div class="centered contact-icons">
      <svg width="15" height="16" viewBox="0 0 15 16" aria-label="Mobile">
        <rect x="3.5" y="1" width="8" height="14" rx="1.5" fill="none" stroke="var(--orange)" stroke-width="1.4"/>
        <circle cx="7.5" cy="12.3" r="0.9" fill="var(--orange)"/>
      </svg>
      <svg width="17" height="16" viewBox="0 0 17 16" aria-label="Email">
        <rect x="1.5" y="3.5" width="14" height="9" fill="none" stroke="var(--orange)" stroke-width="1.4"/>
        <path d="M1.5 3.5 L8.5 9 L15.5 3.5" fill="none" stroke="var(--orange)" stroke-width="1.4"/>
      </svg>
      <svg width="17" height="16" viewBox="0 0 17 16" aria-label="Website">
        <circle cx="8.5" cy="8" r="6.5" fill="none" stroke="var(--orange)" stroke-width="1.2"/>
        <ellipse cx="8.5" cy="8" rx="3" ry="6.5" fill="none" stroke="var(--orange)" stroke-width="1.1"/>
        <path d="M2 8 H15 M3 4.6 H14 M3 11.4 H14" stroke="var(--orange)" stroke-width="1.1"/>
      </svg>
    </div>

    <div class="centered detail detail--phone">+61 400 278 913</div>
    <div class="centered detail detail--mail">rhea@jarvisart.com</div>
    <div class="centered detail detail--web">www.<span class="accent">rheajarvis</span>.com</div>

    <p class="centered offer">Original Fine Artworks for sale<br>online, art galleries etc<br>Custom made to order and by commission.</p>
  </section>

  <section class="card card--back">
    <svg class="card__bg" viewBox="0 0 446 781" width="446" height="781">
      <rect width="446" height="781" fill="var(--orange)"/>
      <path d="M0 192 A278 278 0 0 1 446 192 L446 746 L0 746 Z" fill="var(--black)"/>
      <path d="M0 192 A278 278 0 0 1 446 192" fill="none" stroke="var(--white)" stroke-width="6"/>
      <rect x="0" y="746" width="446" height="35" fill="var(--black)"/>
      <rect x="0" y="746" width="80" height="35" fill="var(--white)"/>
      <rect x="86" y="746" width="274" height="35" fill="var(--orange)"/>
      <rect x="366" y="746" width="80" height="35" fill="var(--white)"/>
    </svg>
    <div class="centered back-name">Rhea Jarvis</div>
    <div class="centered back-web">www.<span class="accent">rheajarvis</span>.com</div>
  </section>

</main>
</body>
</html>
```